Schlichtes Design für Malerbetrieb
Zielgruppe
Wir sind ein mittelgroßer Malerbetrieb in München mit umfangreichem Leistungsspektrum.
Unsere Hauptleistungen sind: Fassadenrenovierung, Altbausanierung, Betoninstandsetzung, Balkonabdichtung (kein Neubau!).
Unsere Zielgruppen sind: Hausverwaltungen, Firmen und Privatpersonen.
Unsere Kunden schätzen: Konstruktive Organisation und Planung im Vorfeld, Zuverlässigkeit, saubere Arbeitsweise, dauerhafte Balkonabdichtungen.
Aufgabenstellung
Wir möchten eine langlebige, stilvolle, minimalistische Homepage.
Wir möchten von der bestehenden Homepage nur die Schriftart für unseren Firmennamen (Century Gothic) und wenn möglich (nicht zwingend), irgendwo das florale Muster einbauen. Corporate-Design haben wir nicht.
Farbtöne: Firmennamen Orange (hellorange bis erdiges Orange möglich, da sind wir nicht fixiert) , einen dunklen Hintergrundfarbton (Petrol-Blaugrau ?) mit gelbem (neon bis senfgelb) Akzent (Linien), Blumenmuster weiß, grau.
Dies sind nur unsere Ideen. Wir sind aber auch absolut offen für eure Profi-Ideen.
Wir möchten uns von den unzähligen langweiligen 'Pinselseiten mit veralteten Bilder' unserer Kollegen interessant und mit Stil abheben.
Eher nach dem Motto 'weniger ist mehr'.
Einen positiven, sympathischen Eindruck geben und unsere Leistungen in den Vordergrund bringen.
Da wir viele Stammkunden haben, betreiben wir kein Social-Media und möchten dies vorerst auch nicht tun.
Die Seite wird in den nächsten Jahren nicht verändert, höchstens die Bilder aktualisiert.
Die Texte haben wir alle selbst entworfen und möchten wir so übernehmen.
Die Galerien sollen unkompliziert anzuschauen sein.
Uns gefällt die Struktur und Schlichtheit von https://vaartmolen.nl/ oder Timbra.de gut und wir mögen Vintage-Grafiken gerne.
Einerseits darf die Seite geradlinig, andererseits aber auch rund und floral wirken.

```html
<!DOCTYPE html>
<html lang="de">
<head>
<meta charset="utf-8">
<title>kolbrit malerarbeiten – Start</title>
<link rel="stylesheet" href="https://fonts.googleapis.com/css2?family=Questrial&family=Montserrat:ital,wght@0,400;0,600;1,700&display=swap">
<style>
  :root {
    --petrol: #1f3f52;
    --petrol-deep: #183444;
    --accent: #d2d400;
    --paper: #f5f5f4;
    --ink: #2b2b2b;
    --white: #ffffff;
    --hero-a: #d9dcdf;
    --hero-b: #8f918d;
    --hero-c: #5a4d40;
  }
  * { box-sizing: border-box; margin: 0; padding: 0; }
  html, body { width: 1200px; height: 720px; overflow: hidden; background: var(--paper); }
  body { font-family: "Montserrat", sans-serif; color: var(--ink); }

  .site-header {
    height: 78px;
    background: var(--petrol);
    display: flex;
    align-items: center;
    padding: 0 70px 0 110px;
  }
  .brand { display: flex; flex-direction: column; align-items: flex-end; line-height: 1; color: var(--accent); font-family: "Questrial", sans-serif; }
  .brand-name { font-size: 34px; letter-spacing: 0.5px; }
  .brand-tag { font-size: 10px; margin-top: 1px; }

  .main-nav { margin-left: auto; display: flex; align-items: center; gap: 44px; height: 100%; }
  .main-nav a {
    font-family: "Montserrat", sans-serif;
    font-style: italic;
    font-weight: 700;
    font-size: 11px;
    letter-spacing: 1px;
    color: var(--accent);
    text-decoration: none;
    text-transform: uppercase;
  }
  .main-nav a.is-active {
    background: var(--accent);
    color: var(--petrol-deep);
    height: 100%;
    display: flex;
    align-items: center;
    padding: 0 22px;
    margin-right: -20px;
  }

  .hero {
    position: relative;
    height: 342px;
    overflow: hidden;
  }
  .hero-photo { position: absolute; inset: 0; width: 100%; height: 100%; }
  .hero-copy { position: absolute; left: 110px; top: 74px; color: var(--white); font-family: "Questrial", sans-serif; }
  .hero-title { font-size: 44px; font-weight: 400; letter-spacing: 1.5px; }
  .hero-lead { font-size: 17px; letter-spacing: 0.8px; margin-top: 4px; }
  .hero-button {
    display: inline-block;
    margin-top: 22px;
    background: var(--petrol);
    color: var(--white);
    font-family: "Montserrat", sans-serif;
    font-weight: 600;
    font-size: 13px;
    letter-spacing: 0.5px;
    padding: 9px 26px;
    border-radius: 2px;
    text-decoration: none;
  }
  .hero-arrow { position: absolute; top: 150px; width: 22px; height: 36px; }
  .hero-arrow.next { right: 40px; }
  .hero-arrow.prev { left: 20px; opacity: 0.7; }
  .hero-dots { position: absolute; left: 50%; bottom: 24px; transform: translateX(-50%); display: flex; gap: 18px; color: var(--white); font-size: 12px; font-family: "Questrial", sans-serif; }
  .hero-dots span { border-bottom: 1px solid var(--white); padding: 0 2px 1px; }

  .intro { padding: 40px 110px 0 150px; }
  .intro-title { font-family: "Questrial", sans-serif; font-weight: 400; font-size: 38px; line-height: 1.15; letter-spacing: 1.5px; color: var(--ink); }
  .intro-title .highlight { color: var(--accent); }
  .intro-text { margin-top: 24px; max-width: 900px; font-size: 11.5px; line-height: 1.7; color: var(--ink); }
</style>
</head>
<body>
  <header class="site-header">
    <div class="brand">
      <span class="brand-name">kolbrit</span>
      <span class="brand-tag">malerarbeiten</span>
    </div>
    <nav class="main-nav">
      <a href="#" class="is-active">Start</a>
      <a href="#">Leistungen</a>
      <a href="#">Portrait</a>
      <a href="#">Auszeichnung</a>
      <a href="#">Karriere</a>
      <a href="#">Kontakt</a>
    </nav>
  </header>

  <section class="hero">
    <svg class="hero-photo" role="img" aria-label="Foto eines hellen, frisch gestrichenen Altbau-Innenraums mit Fenstertüren und Esstisch" viewBox="0 0 1200 342" preserveAspectRatio="none">
      <defs>
        <linearGradient id="heroTone" x1="0" y1="0" x2="0" y2="1">
          <stop offset="0" stop-color="var(--hero-a)"/>
          <stop offset="0.6" stop-color="var(--hero-b)"/>
          <stop offset="1" stop-color="var(--hero-c)"/>
        </linearGradient>
      </defs>
      <rect width="1200" height="342" fill="url(#heroTone)"/>
    </svg>
    <svg class="hero-arrow prev" viewBox="0 0 22 36"><polyline points="18,3 4,18 18,33" fill="none" stroke="#ffffff" stroke-width="3"/></svg>
    <svg class="hero-arrow next" viewBox="0 0 22 36"><polyline points="4,3 18,18 4,33" fill="none" stroke="#ffffff" stroke-width="3"/></svg>
    <div class="hero-copy">
      <h1 class="hero-title">Malerarbeiten in Perfektion.</h1>
      <p class="hero-lead">Qualität kennt keine Kompromisse. Professionelle Malerarbeiten</p>
      <a href="#" class="hero-button">Mehr dazu</a>
    </div>
    <div class="hero-dots"><span>1</span><span>2</span><span>3</span></div>
  </section>

  <section class="intro">
    <h2 class="intro-title">Aus dem Chaos<br>zur <span class="highlight">Ordnung.</span></h2>
    <p class="intro-text">Lorem ipsum dolor sit amet, consectetur adipisicing elit, sed do eiusmod tempor incididunt ut labore et dolore magna aliqua. Ut enim ad minim veniam, quis nostrud exercitation ullamco laboris nisi ut aliquip ex ea commodo consequat. Duis aute irure dolor in reprehenderit in voluptate velit esse cillum dolore eu fugiat nulla pariatur. Excepteur sint occaecat cupidatat non proident, sunt in culpa qui officia deserunt mollit anim id est laborum.</p>
  </section>
</body>
</html>
```